BrimFalcon Business Cards

We have a defined brand. Please visit our website to get a feel for the product and the color pallets. www.brimfalcon-example.com

We need an updated, world class business card design. (See the attached existing card design). Please utilize BOTH sides of the card as shown and be creative with the layout. I do want the horse head icon to be positioned as it is with the existing card.

The remainder of the layout can be customized and I also want it vertically oriented.

Attached are the logo files and please use the colors as follows:
Green - #A5CE39
Tan - #CDBD99
Black

Feel free to play with the colors.

```html
<!DOCTYPE html>
<html lang="en">
<head>
<meta charset="utf-8">
<title>BrimFalcon Business Card</title>
<link href="https://fonts.googleapis.com/css2?family=Roboto:wght@400;700&family=Roboto+Condensed:wght@700&display=swap" rel="stylesheet">
<style>
  :root {
    --green: #A5CE39;
    --black: #0c0c0c;
    --white: #ffffff;
    --backdrop: #3a3a3a;
  }
  * { box-sizing: border-box; margin: 0; padding: 0; }
  html, body { width: 1200px; height: 1108px; overflow: hidden; }
  body {
    background: var(--backdrop);
    font-family: "Roboto", Arial, sans-serif;
    position: relative;
  }
  .card {
    position: absolute;
    top: 234px;
    width: 400px;
    height: 640px;
    border-radius: 24px;
    overflow: hidden;
  }
  .card--front { left: 160px; background: var(--black); }
  .card--back { left: 640px; background: var(--green); }

  .front-shapes { position: absolute; inset: 0; }

  .brand {
    position: absolute;
    top: 110px;
    left: 0; right: 0;
    display: flex;
    justify-content: center;
    align-items: center;
    gap: 10px;
  }
  .brand__dot {
    width: 34px; height: 34px;
    border-radius: 50%;
    background: var(--black);
  }
  .brand__name {
    font-family: "Roboto", Arial, sans-serif;
    font-weight: 700;
    font-size: 36px;
    color: var(--black);
    letter-spacing: 0.5px;
  }

  .contact {
    position: absolute;
    top: 402px;
    left: 0; right: 0;
    text-align: center;
    color: var(--white);
  }
  .contact__name {
    font-family: "Roboto Condensed", Arial, sans-serif;
    font-weight: 700;
    font-size: 34px;
    color: var(--green);
    line-height: 1;
  }
  .contact__title {
    font-weight: 700;
    font-size: 15px;
    margin-top: 4px;
  }
  .contact__rule {
    width: 34px;
    height: 1px;
    background: var(--green);
    margin: 12px auto 12px;
  }
  .contact__lines {
    font-size: 15.5px;
    line-height: 1.38;
  }

  .mark {
    position: absolute;
    top: 140px;
    left: 65px;
    width: 270px;
    height: 270px;
    border-radius: 50%;
    background: var(--black);
  }
  .tagline {
    position: absolute;
    top: 525px;
    left: 0; right: 0;
    text-align: center;
    font-family: "Roboto Condensed", Arial, sans-serif;
    font-weight: 700;
    font-size: 30px;
    color: var(--black);
  }
</style>
</head>
<body>
  <section class="card card--front">
    <svg class="front-shapes" viewBox="0 0 400 640" width="400" height="640" aria-hidden="true">
      <path d="M0 225 C70 360 270 390 400 305 L400 318 C270 410 60 400 0 285 Z" fill="var(--green)"/>
      <path d="M0 0 H400 V298 C280 372 80 350 0 210 Z" fill="var(--white)"/>
    </svg>
    <div class="brand">
      <span class="brand__dot"></span>
      <span class="brand__name">BrimFalcon</span>
    </div>
    <div class="contact">
      <h1 class="contact__name">DEREK MALLOY</h1>
      <p class="contact__title">President &amp; CEO</p>
      <div class="contact__rule"></div>
      <p class="contact__lines">
        BrimFalcon Labs LLC<br>
        Northvale, Saskatchewan Canada<br>
        306.555.0148 | derek@brimfalcon-example.com<br>
        brimfalconlabs-example.com
      </p>
    </div>
  </section>

  <section class="card card--back">
    <div class="mark" role="img" aria-label="BrimFalcon brand symbol"></div>
    <p class="tagline">Mobility Reimagined</p>
  </section>
</body>
</html>
```